BrivoTerna. Lantern of the Steady Harvest. Business card

Professional business card for BrivoTerna (Lantern of the Steady Harvest)
My rationale: Strategy-> Execution-> Results-> Value that lead to the BrivoTerna name: We put the Lantern of the Steady Harvest.
We deliver value to our customers helping them at defining a good strategy (cyan arrow). 90% of well formulated strategies fail due to poor execution so we also consider strategical execution very important (green arrow). Due to the execution we obtain the results (blue arrow). Finally, the results provide feedback to redefine strategy, and the new strategy has to be executed and new results obtained providing new feedback and on and on. It's like a wheel that finally, must create corporate value: value for shareholders, staholders, employees, providers...-

Target Market(s)

CEOs and steering comitees , invewrnent funds

Industry/Entity Type

Business Consultant

Contact Information for Business Card

Teodoro Vinsquel
CEO & Founder
teodoro.vinsquel@brivoterna-example.com
Mobile: +34 655.803.912
www.brivoterna-example.com

Colors

Designer to choose colors to be used in the design.

Requirements
Nice to have
• Nice to hace the words: Strategy, execution, results
• Nice to vave the claim: Lantern of the Steady Harvest
• The three colors should be shown:
• cyan for STRATEGY
• green for EXECUTION
• blue for RESULTS
Should not have
• Complete black background

```html
<!DOCTYPE html>
<html lang="en">
<head>
<meta charset="utf-8">
<title>BrivoTerna – Business Card</title>
<link href="https://fonts.googleapis.com/css2?family=Montserrat:wght@400;500;700;800&display=swap" rel="stylesheet">
<style>
  :root {
    --backdrop: #d9d9d7;
    --card-white: #ffffff;
    --brand-blue: #213f9a;
    --brand-green: #8dc63f;
    --brand-cyan: #29b0e6;
    --text-grey: #555a60;
    --on-blue: #f4f5f8;
  }
  * { box-sizing: border-box; margin: 0; padding: 0; }
  html, body {
    width: 1200px; height: 801px; overflow: hidden;
    background: var(--backdrop);
    font-family: "Montserrat", sans-serif;
  }
  .sheet {
    width: 1200px; height: 801px;
    display: flex; align-items: center; justify-content: center; gap: 40px;
  }
  .card {
    width: 540px; height: 309px;
    position: relative;
    box-shadow: 0 8px 22px rgba(0,0,0,0.18);
  }
  /* Front: contact side */
  .card--front {
    background: var(--card-white);
    display: flex; align-items: center;
  }
  .front__brand {
    width: 220px;
    display: flex; justify-content: center;
  }
  .brand-name {
    font-weight: 800; color: var(--brand-blue);
    font-size: 32px; letter-spacing: -0.5px;
  }
  .front__divider {
    width: 2px; height: 150px; background: var(--brand-cyan);
  }
  .front__contact { padding-left: 26px; }
  .person-name {
    font-weight: 700; color: var(--brand-blue); font-size: 19px;
  }
  .person-role {
    font-weight: 500; color: var(--brand-green); font-size: 14px;
    margin: 3px 0 16px;
  }
  .contact-list { list-style: none; }
  .contact-item {
    display: flex; align-items: center; gap: 8px;
    color: var(--text-grey); font-size: 11.2px; line-height: 1.75;
  }
  .contact-icon { width: 12px; height: 12px; flex: none; }
  /* Back: brand side */
  .card--back {
    background: linear-gradient(160deg, #2544a0 0%, var(--brand-blue) 55%, #1a3088 100%);
    display: flex; flex-direction: column; align-items: center; justify-content: center;
  }
  .card--back .brand-name {
    color: var(--on-blue); font-size: 58px; letter-spacing: -1px;
  }
  .tagline {
    display: flex; gap: 18px; margin-top: 14px;
    color: var(--on-blue); font-weight: 500; font-size: 17px; letter-spacing: 0.5px;
  }
  .tagline__item { display: flex; align-items: center; gap: 7px; }
  .tagline__item::before {
    content: ""; width: 8px; height: 8px; background: var(--brand-green);
  }
</style>
</head>
<body>
<main class="sheet">
  <section class="card card--front" aria-label="Business card, contact side">
    <div class="front__brand"><span class="brand-name">BrivoTerna</span></div>
    <div class="front__divider"></div>
    <div class="front__contact">
      <h1 class="person-name">Teodoro Vinsquel</h1>
      <p class="person-role">CEO &amp; Founder</p>
      <ul class="contact-list">
        <li class="contact-item">
          <svg class="contact-icon" viewBox="0 0 12 12"><rect x="3" y="0.8" width="6" height="10.4" rx="1" fill="none" stroke="#8dc63f" stroke-width="1.2"/><circle cx="6" cy="9.3" r="0.7" fill="#8dc63f"/></svg>
          +34 655.803.912
        </li>
        <li class="contact-item">
          <svg class="contact-icon" viewBox="0 0 12 12"><rect x="0.5" y="2.5" width="11" height="7.5" fill="#8dc63f"/><path d="M0.5 2.5 L6 7 L11.5 2.5" fill="none" stroke="#fff" stroke-width="1"/></svg>
          teodoro.vinsquel@brivoterna-example.com
        </li>
        <li class="contact-item">
          <svg class="contact-icon" viewBox="0 0 12 12"><circle cx="6" cy="6" r="5.5" fill="#8dc63f"/><ellipse cx="6" cy="6" rx="2.3" ry="5.5" fill="none" stroke="#fff" stroke-width="0.8"/><line x1="0.5" y1="6" x2="11.5" y2="6" stroke="#fff" stroke-width="0.8"/></svg>
          www.brivoterna-example.com
        </li>
      </ul>
    </div>
  </section>

  <section class="card card--back" aria-label="Business card, brand side">
    <span class="brand-name">BrivoTerna</span>
    <p class="tagline">
      <span class="tagline__item">Strategy</span>
      <span class="tagline__item">Execution</span>
      <span class="tagline__item">Results</span>
    </p>
  </section>
</main>
</body>
</html>
```